Food and Beverage Business Cards

We need business cards with logo designs for a consultant in the food and beverage industry. We specialize in helping restaurants fix operational and management problems.
Specific areas of expertise include:
-Steps of service
-Staff management tools
-Standard operating procedures
-Profit and loss management
-Inventory
-Point of sales
-Bar Menu
-Mystery shopper service
-Handling and managing suppliers

Target Market(s)

Restaurant and bar owners and managers

Industry/Entity Type

Business

Contact Information for Business Card

Mathieu Girardot
Q&T Consulting
phone: 15027390614
mathqt@sampleinbox.com

Font styles to use
Other font styles liked:
• Check out the screen shot font idea

Colors

Designer to choose colors to be used in the design.

Requirements
Must have
• Must include QR code (See attachment)
• Logo should reflect our specific focus on the drinks side of the industry.
• Areas of Expertise:
• -Service Steps
• -Staff management tools
• -S.O.P
• -P&L Management
• -Inventory
• -P.O.S
• -Bar Menu
• -Mystery Shopper Service
• -Handling and Managing Suppliers

```html
<!DOCTYPE html>
<html lang="en">
<head>
<meta charset="utf-8">
<title>Q&amp;T Consulting Business Cards</title>
<link href="https://fonts.googleapis.com/css2?family=Open+Sans:wght@400;700&display=swap" rel="stylesheet">
<style>
  :root {
    --backdrop: #3a3431;
    --card: #161616;
    --ink: #f2f2f2;
    --ink-soft: #cfcfcf;
    --green-deep: #1f3d22;
    --green-mid: #3f7a34;
    --badge-dark: #3c3c3c;
    --badge-light: #e6e6e6;
  }
  * { box-sizing: border-box; margin: 0; padding: 0; }
  html, body { width: 1200px; height: 864px; overflow: hidden; }
  body {
    background: var(--backdrop);
    font-family: "Open Sans", Arial, sans-serif;
    color: var(--ink);
    display: flex;
    flex-direction: column;
    align-items: center;
    justify-content: center;
    gap: 24px;
  }
  .card {
    width: 720px;
    height: 400px;
    background: var(--card);
    position: relative;
    box-shadow: 0 10px 30px rgba(0,0,0,.45);
  }

  /* Expertise side */
  .art-placeholder {
    position: absolute;
    border-radius: 8px;
    background: radial-gradient(circle at 50% 45%, var(--green-mid), var(--green-deep));
  }
  .art-placeholder--main { left: 270px; top: 42px; width: 170px; height: 140px; }
  .art-placeholder--small { left: 470px; top: 78px; width: 64px; height: 52px; }
  .badges {
    position: absolute;
    left: 548px;
    top: 70px;
    display: flex;
    gap: 8px;
  }
  .badge { width: 60px; height: 60px; border-radius: 50%; }
  .badge--dark { background: var(--badge-dark); border: 3px solid var(--badge-light); }
  .badge--light { background: var(--badge-light); }
  .expertise {
    position: absolute;
    left: 0;
    right: 0;
    top: 212px;
    text-align: center;
  }
  .expertise-title {
    font-size: 24px;
    font-weight: 700;
    margin-bottom: 10px;
  }
  .expertise-list {
    font-size: 17px;
    line-height: 1.45;
    color: var(--ink-soft);
  }

  /* Contact side */
  .contact-card { display: flex; align-items: center; }
  .brand {
    width: 370px;
    text-align: center;
    font-size: 72px;
    font-weight: 700;
    line-height: 1;
    color: var(--ink);
  }
  .divider {
    width: 2px;
    height: 150px;
    background: var(--ink-soft);
  }
  .person { padding-left: 34px; }
  .person-name {
    font-size: 22px;
    font-weight: 700;
    text-transform: uppercase;
  }
  .person-role {
    font-size: 18px;
    text-transform: uppercase;
    margin-bottom: 12px;
  }
  .contact-line {
    display: flex;
    align-items: center;
    gap: 10px;
    font-size: 18px;
    line-height: 1.5;
  }
  .contact-line svg { width: 16px; height: 16px; fill: var(--ink); flex: none; }
</style>
</head>
<body>
  <section class="card expertise-card">
    <div class="art-placeholder art-placeholder--main" role="img" aria-label="Green circuit-pattern speech bubble illustration"></div>
    <div class="art-placeholder art-placeholder--small" role="img" aria-label="Small green circuit-pattern speech bubble illustration"></div>
    <div class="badges">
      <div class="badge badge--dark"></div>
      <div class="badge badge--light"></div>
    </div>
    <div class="expertise">
      <h2 class="expertise-title">Areas of Expertise</h2>
      <p class="expertise-list">
        Service Steps | Staff management tools | S.O.P | P&amp;L Management<br>
        Inventory | P.O.S | Bar Menu | Mystery Shopper Service<br>
        Handling and Managing Suppliers
      </p>
    </div>
  </section>

  <section class="card contact-card">
    <div class="brand">Q&amp;T Studio</div>
    <div class="divider"></div>
    <div class="person">
      <p class="person-name">Mathieu Girardot</p>
      <p class="person-role">Q&amp;T Consulting</p>
      <p class="contact-line">
        <svg viewBox="0 0 16 16" aria-hidden="true"><path d="M1 5 C1 2 15 2 15 5 L15 7 L11 7 L11 5 L5 5 L5 7 L1 7 Z M3 9 L13 9 L14 15 L2 15 Z"/></svg>
        15027390614
      </p>
      <p class="contact-line">
        <svg viewBox="0 0 16 16" aria-hidden="true"><path d="M1 3 L15 3 L8 9 Z M1 5 L8 11 L15 5 L15 13 L1 13 Z"/></svg>
        mathqt@sampleinbox.com
      </p>
    </div>
  </section>
</body>
</html>
```